Harborview Estates Business Card for Apartment Buildings

Create business cards for resident managers who run apartment buildings. The audience is the public who are searching for apartment rentals, and current residents who live at the apartment building. Key design element will be incorporating the company logo, however, the logo cannot dominate. The building name and manager name are more important than the logo. Current business card design leaves little room for copy, so we may need to reduce the size on the current card to allow for more space for copy.

Target Market(s)

Adults 18-65 years of age, who are looking for an apartment rental, plus current residents who live at our apartment buildings.

Industry/Entity Type

Property Management

Contact Information for Business Card

A major design element will be use of the company logo. Important property and manager contact information must be part of the design. The size of the logo will need to be reduced to make room for building and manager contact copy.

Font styles to use
Sans Serif

Colors
3176b5
000000
959595
ffffff

Requirements
Must have
• 1) Incorporate the company logo.
• 2) Use the company colors (dark blue, black/grey, over white).
• 3) FEATURE THE BUILDING NAME
• 4) FEATURE THE MANAGER NAME
• 5) The company name is less important than BUILDING and MANAGER
• 6) Manager contact information
• **SEE ATTACHED CREATIVE BRIEF**
Nice to have
• 1) Back of card logo watermark
• 2) Ability to write notes on back of carfd
Should not have
• Avoid letting the company logo dominate the card, the building name and manager are more important than the company logo.

```html
<!DOCTYPE html>
<html lang="en">
<head>
<meta charset="utf-8">
<title>Harborview Estates – Resident Manager Business Card</title>
<link rel="stylesheet" href="https://fonts.googleapis.com/css2?family=Roboto+Condensed:wght@500;700&family=Roboto:wght@400;500&display=swap">
<style>
  :root {
    --brand-blue: #1569a8;
    --brand-grey: #4a4a4a;
    --paper: #f3f3f3;
    --white: #ffffff;
    --stage: #2b2b2b;
  }
  * { margin: 0; padding: 0; box-sizing: border-box; }
  html, body { width: 1200px; height: 960px; overflow: hidden; }
  body {
    background: var(--stage);
    font-family: "Roboto", Arial, sans-serif;
    position: relative;
  }
  .card {
    position: absolute;
    left: 320px;
    width: 600px;
  }
  .card-back {
    top: 108px;
    height: 334px;
    background: var(--brand-blue);
  }
  .card-front {
    top: 493px;
    height: 342px;
    background: var(--paper);
  }
  .company-mark {
    position: absolute;
    top: 56px;
    left: 0;
    width: 100%;
    display: flex;
    justify-content: center;
    align-items: center;
    gap: 12px;
  }
  .company-mark__square {
    width: 26px;
    height: 26px;
    background: var(--brand-blue);
  }
  .company-mark__name {
    font-family: "Roboto Condensed", Arial, sans-serif;
    font-weight: 700;
    font-size: 30px;
    letter-spacing: 1px;
    color: var(--brand-blue);
    text-transform: uppercase;
  }
  .contact-band {
    position: absolute;
    left: 0;
    bottom: 0;
    width: 100%;
    height: 130px;
    background: var(--brand-blue);
    color: var(--white);
    display: flex;
    justify-content: space-between;
    padding: 12px 30px 0 29px;
  }
  .manager-name {
    font-family: "Roboto Condensed", Arial, sans-serif;
    font-weight: 700;
    font-size: 23px;
    line-height: 26px;
  }
  .manager-title {
    font-size: 15px;
    line-height: 20px;
    margin-bottom: 5px;
  }
  .building-name {
    font-weight: 500;
    font-size: 15px;
    line-height: 19px;
  }
  .building-address {
    font-size: 14.5px;
    line-height: 19px;
  }
  .contact-list {
    list-style: none;
    padding-top: 11px;
    text-align: right;
  }
  .contact-list li {
    font-size: 14px;
    line-height: 19.3px;
    display: flex;
    justify-content: flex-end;
    align-items: center;
    gap: 8px;
  }
  .contact-list svg {
    width: 13px;
    height: 13px;
    fill: var(--white);
    flex: none;
  }
</style>
</head>
<body>
  <section class="card card-back" aria-label="Card back"></section>

  <section class="card card-front" aria-label="Card front">
    <div class="company-mark">
      <span class="company-mark__square"></span>
      <span class="company-mark__name">Harborview Estates LLC</span>
    </div>

    <div class="contact-band">
      <div class="manager-block">
        <p class="manager-name">Marisol Delgado</p>
        <p class="manager-title">Resident Manager</p>
        <p class="building-name">Cedar Court Apartments</p>
        <p class="building-address">2845 Linden Avenue</p>
        <p class="building-address">Bayside, CA 90000</p>
      </div>
      <ul class="contact-list">
        <li>555-210-4830
          <svg viewBox="0 0 16 16" aria-hidden="true"><path d="M3.6 1l2.6 2.6-1.5 2a9 9 0 0 0 5 5l2-1.5L14.3 11.7 12.5 14C6.4 14 2 9.6 2 3.5z"/></svg></li>
        <li>555-347-9162
          <svg viewBox="0 0 16 16" aria-hidden="true"><path d="M4 0h8v16H4zM5.5 2v10h5V2zM7 13.2h2v1.4H7z" fill-rule="evenodd"/></svg></li>
        <li>555-408-2275
          <svg viewBox="0 0 16 16" aria-hidden="true"><path d="M4 1h7l1 1v4H4zM1 7h14v6h-2v2H3v-2H1zM4.5 11v2.5h7V11z" fill-rule="evenodd"/></svg></li>
        <li>marisol@harborviewest.com
          <svg viewBox="0 0 16 16" aria-hidden="true"><path d="M1 3h14v10H1zM2.5 4.5L8 8.6l5.5-4.1z" fill-rule="evenodd"/></svg></li>
        <li>www.harborviewest.com
          <svg viewBox="0 0 16 16" aria-hidden="true"><path d="M8 1a7 7 0 1 0 0 14A7 7 0 0 0 8 1zM5 4.5c1 .3 1.5 1.4 2.6 1.2.8.6 0 1.7 1 2.4.8.4.6 1.8-.2 2.5-.6 1-.3 2.2-1 2.6-.6-1.5-1.6-2.6-1.4-4-1-.3-2.3-1-2.3-2.2C3.7 6 4.4 5 5 4.5zm5-1.5c1.2.4 2.3 1.3 2.8 2.5-.9.1-1.7-.4-2.2-1z" fill-rule="evenodd"/></svg></li>
      </ul>
    </div>
  </section>
</body>
</html>
```